DL Flyer Design

I need a DL flyer, double-sided designed for a Brisbane based outdoor group exercise/training company called Rise Up! Rise Up! provides group outdoor training, designed for the individual. It provides the support, motivation and one-on-one attention of personal training combined with the support of a group environment. The classes are fun, challenging and aim to develop confidence & fitness. Weight loss is not the focus, although it is a benefit.
Updates

Hi

I've just uploaded a high res version of the logo if you need.

Cheers
Tam

Target Market(s)

English speaking men & women aged 25 - 45, white-collar office jobs. Average-low level of fitness, not hugely 'fitness' oriented but want to improve quality of life, overall fitness, lose a bit of weight.

Computer and consumer literate. Live in suburban Brisbane, Australia.

Industry/Entity Type

Training

Requirements
Must have
• Double sided DL. Use of black, greens and white per attached photos. Use of 1300 517 904 (1300 RISE UP) and website www.riseupfitclub.example.com.au

Indicative copy and contents is posted in the comments section.

```html
<!DOCTYPE html>
<html lang="en">
<head>
<meta charset="utf-8">
<title>Rise Up! DL Flyer – Front and Back</title>
<link rel="stylesheet" href="https://fonts.googleapis.com/css2?family=Anton&family=Archivo+Black&family=Open+Sans:wght@400;600&display=swap">
<style>
  :root {
    --canvas: #ffffff;
    --paper: #fbf8e4;
    --frame: #1f5e2e;
    --ink: #111111;
    --green-dark: #2f6b12;
    --green-mid: #3f8f1e;
    --green-bright: #8ccc3f;
    --green-logo: #1fbf5a;
    --sun: #f2dc6a;
    --sun-soft: #f7eca6;
    --teal-soft: #bfe0d8;
    --pink: #e8245a;
    --white: #ffffff;
    --table-line: #2e8b45;
    --table-head: #3a9a52;
  }
  * { box-sizing: border-box; margin: 0; padding: 0; }
  html, body { width: 1200px; height: 838px; overflow: hidden; background: var(--canvas); }
  .canvas { position: relative; width: 1200px; height: 838px; }

  .flyer {
    position: absolute; top: 64px; width: 340px; height: 710px;
    background: var(--paper); border: 4px solid var(--frame); overflow: hidden;
    font-family: "Anton", "Impact", sans-serif; text-align: center;
  }
  .flyer--front { left: 222px; }
  .flyer--back { left: 638px; }

  .flyer__decor { position: absolute; left: 0; top: 0; width: 100%; height: 440px; }

  .kicker {
    position: absolute; top: 52px; left: 0; width: 100%;
    font-family: "Archivo Black", "Arial Black", sans-serif; font-size: 16px; color: var(--ink);
    letter-spacing: 0.2px;
  }
  .lead-in {
    position: absolute; top: 84px; left: 30px; font-size: 27px; color: var(--white);
    text-shadow: 2px 2px 0 var(--ink), -1px -1px 0 var(--ink), 1px -1px 0 var(--ink), -1px 1px 0 var(--ink);
    transform: rotate(-4deg);
  }
  .hero-figure { position: absolute; left: 14px; top: 150px; width: 120px; height: 150px; }
  .brand-name {
    position: absolute; left: 112px; top: 118px; width: 220px;
    font-size: 78px; line-height: 1; color: var(--green-logo); text-align: left;
  }
  .tagline {
    position: absolute; top: 300px; left: 34px; width: 290px;
    font-size: 21px; line-height: 1.05; color: var(--white);
    text-shadow: 2px 2px 0 var(--ink), -1px -1px 0 var(--ink), 1px -1px 0 var(--ink), -1px 1px 0 var(--ink);
    transform: rotate(5deg);
  }
  .flyer--back .tagline { top: 288px; }

  .intro {
    position: absolute; top: 396px; left: 20px; width: 300px;
    font-size: 12.5px; line-height: 14px; color: var(--green-mid); text-transform: uppercase;
  }
  .intro p + p { margin-top: 8px; }
  .offer {
    position: absolute; top: 532px; left: 20px; width: 300px;
    font-size: 21px; line-height: 22px; color: var(--green-mid); text-transform: uppercase;
  }
  .offer__note { display: block; font-family: "Open Sans", sans-serif; font-weight: 600; font-size: 7px; line-height: 9px; color: var(--ink); margin-top: 3px; }

  .cta { position: absolute; left: 0; width: 100%; }
  .cta__call { font-family: "Archivo Black", "Arial Black", sans-serif; color: var(--ink); }
  .cta__phone { color: var(--green-dark); }
  .cta__or { font-size: 0.5em; }
  .cta__web { font-family: "Archivo Black", "Arial Black", sans-serif; color: var(--green-dark); text-transform: uppercase; }

  .flyer--front .cta { top: 594px; }
  .flyer--front .cta__call { font-size: 19px; line-height: 22px; }
  .flyer--front .cta__phone { font-size: 24px; line-height: 26px; }
  .flyer--front .cta__web { font-size: 9.5px; line-height: 13px; margin-top: 5px; }

  .flyer--back .cta { top: 456px; }
  .flyer--back .cta__call { font-size: 34px; line-height: 38px; }
  .flyer--back .cta__phone { font-size: 38px; line-height: 40px; }
  .flyer--back .cta__web { font-size: 10.5px; line-height: 15px; margin-top: 6px; color: var(--ink); }

  .timetable {
    position: absolute; top: 350px; left: 8px; width: 316px;
    border-collapse: collapse; font-family: "Open Sans", sans-serif; font-size: 7px;
    color: var(--green-dark); text-align: left; background: rgba(255,255,255,0.85);
    border: 2px solid var(--table-line);
  }
  .timetable th { background: var(--table-head); color: var(--white); font-weight: 400; padding: 2px 3px; }
  .timetable td { padding: 3px; vertical-align: top; border-top: 1px solid var(--table-line); height: 26px; }
  .timetable td.timetable__time { font-weight: 600; }
</style>
</head>
<body>
<main class="canvas">

  <section class="flyer flyer--front" aria-label="Flyer front">
    <svg class="flyer__decor" viewBox="0 0 340 440" role="img" aria-label="Halftone sun circle with pink paint splashes and teal dot texture behind the headline">
      <defs>
        <radialGradient id="sunFront" cx="50%" cy="50%" r="50%">
          <stop offset="0%" stop-color="var(--sun)"/>
          <stop offset="100%" stop-color="var(--sun-soft)"/>
        </radialGradient>
        <linearGradient id="skyFront" x1="0" y1="0" x2="1" y2="1">
          <stop offset="0%" stop-color="var(--teal-soft)" stop-opacity="0.7"/>
          <stop offset="100%" stop-color="var(--paper)" stop-opacity="0"/>
        </linearGradient>
      </defs>
      <rect width="340" height="440" fill="url(#skyFront)"/>
      <circle cx="150" cy="230" r="150" fill="url(#sunFront)"/>
      <ellipse cx="325" cy="330" rx="26" ry="60" fill="var(--pink)" opacity="0.85"/>
    </svg>

    <p class="kicker">TIRED OF HANGING ABOUT?</p>
    <p class="lead-in">IT'S TIME TO</p>
    <svg class="hero-figure" viewBox="0 0 120 150" role="img" aria-label="Silhouette of a person leaping outdoors">
      <defs>
        <linearGradient id="figFront" x1="0" y1="0" x2="0" y2="1">
          <stop offset="0%" stop-color="#222"/>
          <stop offset="100%" stop-color="#444"/>
        </linearGradient>
      </defs>
      <rect width="120" height="150" rx="10" fill="url(#figFront)"/>
    </svg>
    <h1 class="brand-name">Rise Up!</h1>
    <p class="tagline">WITH GROUP OUTDOOR TRAINING<br>DESIGNED JUST FOR YOU.</p>

    <div class="intro">
      <p>Rise Up! provides the unique combination<br>of the one-on-one attention of<br>personal training with the motivation<br>and support of a group environment.</p>
      <p>Best of all,<br>it's designed to fit fitness<br>into your life –<br>at an affordable price.</p>
    </div>
    <p class="offer">Curious? Give it a shot<br>with a 1 week free trial!
      <span class="offer__note">(GUARANTEED NO HARD SELL AT THE END)</span></p>

    <div class="cta">
      <p class="cta__call">CALL NOW</p>
      <p class="cta__phone">ON 1300 RISE UP<br>(1300 517 904) <span class="cta__or">OR</span></p>
      <p class="cta__web">Email hello@riseupfitclub.example.com.au<br>www.riseupfitclub.example.com.au</p>
    </div>
  </section>

  <section class="flyer flyer--back" aria-label="Flyer back">
    <svg class="flyer__decor" viewBox="0 0 340 440" role="img" aria-label="Halftone sun circle with pink paint splashes and teal dot texture behind the headline">
      <defs>
        <radialGradient id="sunBack" cx="50%" cy="50%" r="50%">
          <stop offset="0%" stop-color="var(--sun)"/>
          <stop offset="100%" stop-color="var(--sun-soft)"/>
        </radialGradient>
        <linearGradient id="skyBack" x1="0" y1="0" x2="1" y2="1">
          <stop offset="0%" stop-color="var(--teal-soft)" stop-opacity="0.7"/>
          <stop offset="100%" stop-color="var(--paper)" stop-opacity="0"/>
        </linearGradient>
      </defs>
      <rect width="340" height="440" fill="url(#skyBack)"/>
      <circle cx="150" cy="210" r="140" fill="url(#sunBack)"/>
      <ellipse cx="14" cy="140" rx="20" ry="34" fill="var(--pink)" opacity="0.85"/>
    </svg>

    <p class="kicker">TIRED OF HANGING ABOUT?</p>
    <p class="lead-in">IT'S TIME TO</p>
    <svg class="hero-figure" viewBox="0 0 120 150" role="img" aria-label="Silhouette of a person leaping outdoors">
      <rect width="120" height="150" rx="10" fill="#2a2a2a"/>
    </svg>
    <h2 class="brand-name">Rise Up!</h2>
    <p class="tagline">WITH GROUP OUTDOOR TRAINING<br>DESIGNED JUST FOR YOU.</p>

    <table class="timetable">
      <thead>
        <tr><th>Time</th><th>Monday</th><th>Tuesday</th><th>Wednesday</th><th>Thursday</th><th>Friday</th><th>Saturday</th></tr>
      </thead>
      <tbody>
        <tr><td class="timetable__time">6.00am</td><td>Cardio</td><td></td><td>Stress-relief (boxing!)</td><td>Cardio</td><td>Stress-relief (boxing!)</td><td>Mash-up</td></tr>
        <tr><td></td><td></td><td></td><td></td><td></td><td></td><td>One-on-One sessions</td></tr>
        <tr><td class="timetable__time">6.00pm</td><td>Strength</td><td>Cardio</td><td>Strength</td><td>Stress-relief (boxing!)</td><td></td><td></td></tr>
      </tbody>
    </table>

    <div class="cta">
      <p class="cta__call">CALL NOW</p>
      <p class="cta__phone">ON 1300 RISE UP<br>(1300 517 904) <span class="cta__or">OR</span></p>
      <p class="cta__web">Email hello@riseupfitclub.example.com.au<br>www.riseupfitclub.example.com.au</p>
    </div>
  </section>

</main>
</body>
</html>
```